Fitness Equipment & Service

I want to make the card eye catching and fun. We are called Corvane Motion Limited and we are based in Wales. We sell, install and service all types of fitness equipment from Skipping ropes, right through the Dumbbells, Kettle bells and Barbells through to state of the art Treadmills, Running Machines and Strength Equipment. We also design and install changing room furniture and lockers.

TYPOGRAPHY
We would like to use Futrura. Futura has an appearance of efficiency and forwardness. The typeface is derived
from simple geometric forms (near-perfect circles, triangles and squares) and is based on strokes of
near-even weight, which are low in contrast. This is most visible in the almost perfectly round stroke of
the o, which is nonetheless slightly ovoid.
The lowercase has tall ascenders, which rise above the cap line. The uppercase
characters present proportions similar to those of classical Roman capitals.

TYPOGRAPHIC CONSIDERATIONS
No Strike though
No Horizontal Scaling
No Drop Shadows
No Effects
Never use less than 120% Leading

OUR CORPORATE COLOURS
BRAND GUIDELINES
We were thinking that our primary colour palette consists of the Acid Green (Pantone 382) and Process Black.

We work closely with tquarly Ltd and would like to include their name on the card somewhere. I have attached images of the other brands that we work with as an idea or the small icons I have included that illustrate what we do?. I have very kindly been given permission to use any of the images off the files that I have included below, so I hope these help. I will include these below. I would be open to suggestions if it made the card more striking Can you do it?
Updates

Hi All, Just wanted to add a few thoughts but you are the guys with the creative visions (thats why are here) We are based in Wales, UK and we would be open to lots of different ideas on a theme but must be eye catching, Bold and FUN. If you can or think that the Welsh or any dragon could be put in there then go for it (its not a must have) We have also added some ideas for colour but again its over to you!! GO FOR IT ! Thanks and look forward to your visions! Owen

Hi All, Just thought I would sen through the contact details that need to be on the card. (if you want to play around with icons instead of the wording twitter, Facebook, go for it): Corvane Motion Limited Owen Pritchard Managing Director Mob: +44 (0)7582 913 406 e-mail: sales@corvanemotion.co.uk Web: Corvanemotion.co.uk twitter: @motionLetterbin Facebook: Corvane Motion Limited

```html
<!DOCTYPE html>
<html lang="en">
<head>
<meta charset="utf-8">
<title>Corvane Motion Limited – Business Card</title>
<link href="https://fonts.googleapis.com/css2?family=Jost:wght@400;500;700&display=swap" rel="stylesheet">
<style>
  :root {
    --navy: #121a55;
    --navy-soft: #2a3690;
    --paper: #ffffff;
    --ink: #1c1c1c;
    --sky: #48a9dd;
    --blue: #2c8fd0;
    --blue-deep: #1f4a7a;
    --steel: #8fa3b3;
    --band: #2f86c0;
    --backdrop: #e9e9ea;
  }
  * { margin: 0; padding: 0; box-sizing: border-box; }
  html, body { width: 1200px; height: 892px; overflow: hidden; }
  body {
    background: var(--backdrop);
    font-family: "Jost", sans-serif;
    position: relative;
  }
  .card {
    position: absolute;
    top: 272px;
    width: 540px;
    height: 348px;
    overflow: hidden;
    border-radius: 4px;
    box-shadow: 0 2px 8px rgba(0,0,0,0.15);
  }
  .card-back { left: 50px; }
  .card-front { left: 610px; background: var(--paper); }
  .card svg.base { position: absolute; inset: 0; }

  /* Front */
  .brand-mark {
    position: absolute; left: 28px; top: 118px;
    display: flex; align-items: center; gap: 14px;
  }
  .brand-dot { width: 74px; height: 74px; border-radius: 50%; background: var(--navy-soft); }
  .brand-name {
    font-weight: 500; font-size: 21px;
    line-height: 1.25; color: var(--navy); width: 130px;
  }
  .holder {
    position: absolute; right: 24px; top: 26px; text-align: right; color: var(--paper);
  }
  .holder-name { font-weight: 700; font-size: 28px; line-height: 1.2; white-space: nowrap; }
  .holder-role { font-weight: 400; font-size: 17px; line-height: 1.25; white-space: nowrap; }
  .contacts {
    position: absolute; right: 24px; top: 226px; list-style: none;
  }
  .contacts li {
    display: flex; justify-content: flex-end; align-items: center; gap: 10px;
    font-size: 14px; line-height: 1.3; color: var(--ink); height: 22px; white-space: nowrap;
  }
  .contact-icon {
    width: 16px; height: 16px; background: var(--navy); border-radius: 2px;
    display: inline-flex; align-items: center; justify-content: center; flex: none;
  }

  /* Back */
  .tile { position: absolute; width: 100px; height: 98px; }
  .photo-strip { position: absolute; }
  .back-name {
    position: absolute; left: 186px; top: 228px; width: 330px;
    font-weight: 500; font-size: 30px; line-height: 1.25;
    color: var(--paper); text-transform: uppercase; letter-spacing: 2px;
  }
</style>
</head>
<body>

<section class="card card-back" aria-label="Card back">
  <div class="photo-strip" role="img" aria-label="Gym equipment photograph in blue tones"
       style="left:300px;top:0;width:240px;height:196px;background:linear-gradient(135deg,#2a5d8f,#2bb3c6 60%,#1e6f9c);"></div>
  <div class="tile" role="img" aria-label="Tile with web icon" style="left:0;top:0;background:var(--blue);"></div>
  <div class="tile" role="img" aria-label="Tile with map icon" style="left:100px;top:0;background:var(--sky);"></div>
  <div class="tile" role="img" aria-label="Gym photograph tile with equipment icon" style="left:200px;top:0;background:var(--blue-deep);"></div>
  <div class="tile" role="img" aria-label="Gym photograph tile with gift icon" style="left:0;top:98px;background:var(--blue-deep);"></div>
  <div class="tile" role="img" aria-label="Tile with kettlebell icon" style="left:100px;top:98px;background:var(--steel);"></div>
  <div class="tile" role="img" aria-label="Tile with service van icon" style="left:200px;top:98px;background:#3b9be0;"></div>
  <div class="photo-strip" role="img" aria-label="Photograph of a person running on a treadmill"
       style="left:0;top:196px;width:170px;height:152px;background:linear-gradient(160deg,#1d3f6e,#0f2646);"></div>
  <div class="photo-strip" style="left:170px;top:196px;width:370px;height:152px;background:var(--band);"></div>
  <p class="back-name">Corvane Motion Limited</p>
</section>

<section class="card card-front" aria-label="Card front">
  <svg class="base" width="540" height="348" viewBox="0 0 540 348" aria-hidden="true">
    <polygon points="170,0 540,0 540,200" fill="var(--navy)"/>
    <line x1="148" y1="0" x2="540" y2="212" stroke="var(--navy)" stroke-width="3"/>
  </svg>
  <div class="brand-mark">
    <span class="brand-dot"></span>
    <span class="brand-name">Corvane Motion Limited</span>
  </div>
  <div class="holder">
    <p class="holder-name">Owen Pritchard</p>
    <p class="holder-role">Managing Director</p>
  </div>
  <ul class="contacts">
    <li>+44 (0)7582 913 406
      <span class="contact-icon">
        <svg width="10" height="10" viewBox="0 0 10 10"><path d="M2 1 L4 1 L4.6 3 L3.5 3.8 Q4.5 5.8 6.2 6.5 L7 5.4 L9 6 L9 8 Q5 9 1.8 5 Q0.8 3 2 1Z" fill="#fff"/></svg>
      </span></li>
    <li>sales@corvanemotion.co.uk
      <span class="contact-icon">
        <svg width="11" height="8" viewBox="0 0 11 8"><rect x="0.5" y="0.5" width="10" height="7" fill="none" stroke="#fff"/><path d="M0.5 0.5 L5.5 4.5 L10.5 0.5" fill="none" stroke="#fff"/></svg>
      </span></li>
    <li>Corvanemotion.co.uk <span class="contact-icon"></span></li>
    <li>@motionLetterbin <span class="contact-icon"></span></li>
    <li>Corvane Motion Limited <span class="contact-icon"></span></li>
  </ul>
</section>

</body>
</html>
```